Business Card Design

Electronic Security Installation Specialists

Check out our website at www.tallbrookllc.com to see what we do.

Industry/Entity Type

Business

Contact Information for Business Card

Tall Brook
Marjorie Hadley
281 Orchard Rise
Mapleton, WV 25871

Colors
3176b5
0455a3
ffffff

```html
<!DOCTYPE html>
<html lang="en">
<head>
<meta charset="utf-8">
<title>Tall Brook — Business Card</title>
<link rel="stylesheet" href="https://fonts.googleapis.com/css2?family=Exo+2:wght@400;500;600&display=swap">
<style>
  :root {
    --brand-blue: #3176b5;
    --brand-navy: #0455a3;
    --deep-navy: #1f3f8f;
    --card-white: #ffffff;
    --ink: #2a2a2a;
    --steel: #8d8f93;
    --steel-dark: #55585c;
    --ring: #c9cbd0;
    --backdrop: #e9ebee;
  }
  * { box-sizing: border-box; margin: 0; padding: 0; }
  html, body {
    width: 1200px; height: 800px; overflow: hidden;
    background: var(--backdrop);
    font-family: "Exo 2", Arial, sans-serif;
  }
  .canvas {
    position: relative; width: 1200px; height: 800px;
    display: flex; align-items: center; justify-content: center;
  }
  .card {
    position: relative; width: 1000px; height: 571px;
    background: radial-gradient(ellipse at 40% 40%, #ffffff 0%, #f3f4f6 70%, #e8e9ec 100%);
    box-shadow: 0 10px 30px rgba(0,0,0,.18);
    overflow: hidden;
  }
  .card__waves { position: absolute; inset: 0; width: 100%; height: 100%; }
  .brand-mark {
    position: absolute; left: 70px; top: 110px;
    width: 200px; height: 200px; border-radius: 50%;
    background: var(--deep-navy);
    border: 6px solid var(--ring);
    display: flex; align-items: center; justify-content: center;
  }
  .brand-mark__name {
    color: var(--card-white); font-size: 34px; font-weight: 500; letter-spacing: .5px;
  }
  .contact {
    position: absolute; right: 52px; top: 42px;
    text-align: right; color: var(--ink); font-style: normal;
  }
  .contact__address { font-size: 23px; line-height: 31px; letter-spacing: .5px; margin-bottom: 16px; }
  .contact__line {
    display: flex; justify-content: flex-end; align-items: center; gap: 10px;
    font-size: 21px; letter-spacing: 1px; height: 42px;
  }
  .contact__line--small { font-size: 17px; letter-spacing: .3px; height: 31px; }
  .contact__icon { width: 22px; height: 22px; fill: var(--steel-dark); flex: none; }
  .person {
    position: absolute; left: 118px; top: 478px; color: var(--card-white);
  }
  .person__name { font-size: 30px; font-weight: 500; letter-spacing: 1px; line-height: 36px; }
  .person__title { font-size: 20px; letter-spacing: 1px; line-height: 26px; margin-top: 2px; }
</style>
</head>
<body>
<main class="canvas">
  <article class="card">
    <svg class="card__waves" viewBox="0 0 1000 571" preserveAspectRatio="none" aria-hidden="true">
      <defs>
        <linearGradient id="band" x1="0" y1="0" x2="1" y2="0">
          <stop offset="0" stop-color="#1f3f8f"/>
          <stop offset=".55" stop-color="#3176b5"/>
          <stop offset="1" stop-color="#0455a3"/>
        </linearGradient>
        <linearGradient id="steel" x1="0" y1="0" x2="1" y2="0">
          <stop offset="0" stop-color="#e4e5e7"/>
          <stop offset=".6" stop-color="#a2a4a8"/>
          <stop offset="1" stop-color="#55585c"/>
        </linearGradient>
      </defs>
      <path d="M540 470 C740 462 900 430 1000 330 L1000 392 C900 452 740 476 540 472 Z" fill="url(#steel)"/>
      <path d="M0 470 C120 420 260 400 420 420 C560 440 620 462 700 458 C820 452 930 425 1000 395 L1000 571 L0 571 Z" fill="url(#band)"/>
      <path d="M0 452 C120 400 260 382 440 402 C260 390 120 408 0 460 Z" fill="#2a4c9c"/>
      <path d="M700 458 C820 452 930 425 1000 395" fill="none" stroke="#ffffff" stroke-width="3"/>
    </svg>

    <div class="brand-mark">
      <span class="brand-mark__name">Tall Brook</span>
    </div>

    <address class="contact">
      <p class="contact__address">281 Orchard Rise<br>Mapleton, WV 25871</p>
      <p class="contact__line">304 555 0182
        <svg class="contact__icon" viewBox="0 0 24 24"><path d="M6.6 10.8a15 15 0 0 0 6.6 6.6l2.2-2.2a1 1 0 0 1 1-.25 11.4 11.4 0 0 0 3.6.57 1 1 0 0 1 1 1V20a1 1 0 0 1-1 1A17 17 0 0 1 3 4a1 1 0 0 1 1-1h3.5a1 1 0 0 1 1 1c0 1.250.2 2.45.57 3.57a1 1 0 0 1-.25 1z"/></svg>
      </p>
      <p class="contact__line">304 555 0183
        <svg class="contact__icon" viewBox="0 0 24 24"><path d="M7 1h10a2 2 0 0 1 2 2v18a2 2 0 0 1-2 2H7a2 2 0 0 1-2-2V3a2 2 0 0 1 2-2zm0 3v14h10V4zm5 15.2a1 1 0 1 0 0 2 1 1 0 0 0 0-2z"/></svg>
      </p>
      <p class="contact__line">304 555 0184
        <svg class="contact__icon" viewBox="0 0 24 24"><path d="M4 8h2v13H4zM8 3h9l3 3v15H8zm2 8v2h2v-2zm4 0v2h2v-2zm-4 4v2h2v-2zm4 0v2h2v-2zM10 5v4h8V7h-2V5z"/></svg>
      </p>
      <p class="contact__line contact__line--small">info@tallbrookllc.com
        <svg class="contact__icon" viewBox="0 0 24 24"><path d="M2 5h20v14H2zm2 2v.5l8 5 8-5V7zm0 2.8V17h16V9.8l-8 5z"/></svg>
      </p>
      <p class="contact__line contact__line--small">www.tallbrookllc.com
        <svg class="contact__icon" viewBox="0 0 24 24"><path d="M12 2a10 10 0 1 0 0 20 10 10 0 0 0 0-20zm6.9 6h-3a15 15 0 0 0-1.3-3.9A8 8 0 0 1 18.9 8zM12 4c.8 1.1 1.5 2.5 1.9 4h-3.8c.4-1.5 1.1-2.9 1.9-4zM4.3 14a8 8 0 0 1 0-4h3.4a16 16 0 0 0 0 4zm.8 2h3a15 15 0 0 0 1.3 3.9A8 8 0 0 1 5.1 16zm3-8h-3a8 8 0 0 1 4.3-3.9A15 15 0 0 0 8.1 8zM12 20c-.8-1.1-1.5-2.5-1.9-4h3.8c-.4 1.5-1.1 2.9-1.9 4zm2.3-6H9.7a14 14 0 0 1 0-4h4.6a14 14 0 0 1 0 4zm.3 5.9a15 15 0 0 0 1.3-3.9h3a8 8 0 0 1-4.3 3.9zm1.7-5.9a16 16 0 0 0 0-4h3.4a8 8 0 0 1 0 4z"/></svg>
      </p>
    </address>

    <div class="person">
      <h1 class="person__name">MARJORIE HADLEY</h1>
      <p class="person__title">INSTALLATION SPECIALIST</p>
    </div>
  </article>
</main>
</body>
</html>
```